πΈ Full Website Redesign on Wix β The Willowmere Atelier (Feminine, Sophisticated, Nature-Inspired)
Business Name: The Willowmere Atelier
Current Site: https://quorvalen.example/Tz8pLmQ (for structure reference only)
Platform: Wix
Business Type: Women-led Canadian online retail business
Location: Canada
π About The Willowmere Atelier
The Willowmere Atelier is a boutique e-commerce store specializing in roses and blooming plants, created for modern plant lovers who appreciate beauty, quality, and storytelling.
We are a small, women-led business in Ontario, Canada, and our audience is primarily women who are drawn to floral aesthetics, a calming user experience, and elevated design.
Our name β The Willowmere Atelier β represents both a curated collection of blooms and a love of thoughtful, meaningful beauty.
π» Project Overview
We are looking for a full website redesign from scratch (built on Wix) that reflects our brand identity: feminine, sophisticated, romantic, and grounded in nature.
The current version of the site was just a test layout β we now want a fresh, cohesive design vision that speaks directly to our female Canadian customer base with a clean, modern, and elegant interface.
This project is not just about functionality β itβs about crafting an experience that feels like a digital floral sanctuary.
π― What We Need
Full website design and development in Wix (you can start fresh)
Custom homepage design with storytelling and a welcoming brand vibe
Pages to include (subject to refinement):
Home
Shop (products will be added by us later)
About
Contact
FAQ / Info
Blog or Guides (optional placeholder)
Sophisticated visual branding:
Muted rose, blush, and earthy tones
Clean, modern layout with elegant typography
Feminine, natural, soft design elements (think floral details, soft lines, minimalism with warmth)
Optimized for both desktop and mobile
Set up global styles (font, color palette, button styles, etc.)
Guidance or setup for product sections using Wixβs eCommerce system
Create beautiful reusable sections (for us to duplicate later as needed)
π· Brand Style
We are aiming for a website that feels like:
A curated botanical boutique
Feminine and warm β but not overly girly
Sophisticated and soft, never cluttered
Clean but not sterile
Relaxed elegance with a focus on natural beauty
Color palette:
Muted rose
Warm blush tones
Cream, soft beige, earthy sage
Very subtle contrast β no stark black-and-white
Typography:
Elegant serif or soft sans-serif pairings
Easy to read but with character
π Technical Info
Platform: Wix
No custom coding required (Wix-native tools preferred)
We will handle product uploads
Weβll provide any imagery you request
π¦ Deliverables
Fully designed Wix website (ready to publish)
All pages complete with consistent design and layout
Mobile-responsive layout
Design system set up for future content (colors, typography, etc.)
Optional: Style guide PDF for brand reference (bonus)
π Timeline
Weβd like the website to be completed within 1-2 weeks after project start. Please let us know your availability.
β
To Apply
Please include:
Portfolio (especially if youβve done Wix, floral, feminine, or nature-inspired work)
A short message on how you'd approach this project
Timeline/availability
We're looking for someone who understands how to design for emotion, beauty, and ease β not just functionality. If you love soft colors, delicate details, and creating meaningful digital experiences for women, we'd love to hear from you.
πΈ Letβs build something beautiful together!
Rose enthusiasts

```html
<!DOCTYPE html>
<html lang="en">
<head>
<meta charset="utf-8">
<title>The Willowmere Atelier</title>
<link rel="stylesheet" href="https://fonts.googleapis.com/css2?family=EB+Garamond:wght@400;500;600&family=Nunito:wght@400;500;600;700&display=swap">
<style>
  :root {
    --blush: #fbefec;
    --blush-deep: #f5e2de;
    --plum: #52324a;
    --plum-dark: #45293e;
    --sage: #53665a;
    --ink: #2b2226;
    --white: #ffffff;
    --rule: #d9cfd3;
  }
  * { box-sizing: border-box; margin: 0; padding: 0; }
  html, body { width: 1200px; height: 3374px; overflow: hidden; }
  body {
    position: relative;
    background: linear-gradient(180deg, #fbedea 0%, #fcf1ee 40%, #f9e9e6 100%);
    font-family: "Nunito", sans-serif;
    color: var(--ink);
  }
  .abs { position: absolute; }
  .serif { font-family: "EB Garamond", serif; }

  /* Header */
  .nav { left: 111px; top: 42px; display: flex; gap: 28px; font-size: 17px; }
  .brand-mark { left: 576px; top: 9px; width: 53px; height: 83px; background: var(--plum); border-radius: 3px; }
  .brand-name { left: 0; width: 1200px; top: 97px; text-align: center; font-family: "EB Garamond", serif; font-weight: 500; font-size: 20px; letter-spacing: 1px; }
  .login { left: 963px; top: 45px; display: flex; align-items: center; gap: 8px; font-size: 16px; }
  .cart { left: 1064px; top: 40px; }

  /* Hero */
  .hero-photo { left: 111px; top: 132px; width: 978px; height: 551px;
    background: radial-gradient(ellipse at 65% 40%, #d9a98a 0%, #b78b66 18%, #6f7a44 45%, #4a5a2c 75%, #3c4a24 100%); }
  .promo { left: 182px; top: 635px; width: 835px; height: 103px; background: var(--plum); color: var(--white); }
  .promo-index { left: 43px; top: 32px; font-size: 30px; font-weight: 600; letter-spacing: 2px; }
  .promo-text { left: 162px; top: 39px; font-size: 19px; font-weight: 600; }
  .btn-light { left: 638px; top: 27px; width: 153px; height: 48px; background: var(--white); color: var(--plum); font-size: 15px; font-weight: 600; display: flex; align-items: center; justify-content: center; border-radius: 2px; letter-spacing: .5px; }

  /* Potted feature */
  .feature { left: 111px; top: 838px; width: 978px; height: 490px; border: 1px solid #f0dfdb; }
  .feature-left { left: 0; top: 0; width: 488px; height: 488px; background: #fdf3f1; }
  .shot-a { left: 21px; top: 83px; width: 215px; height: 304px; background: linear-gradient(160deg, #efe4d6 0%, #c9b49a 55%, #8f9a6c 100%); }
  .shot-b { left: 250px; top: 83px; width: 214px; height: 304px; background: linear-gradient(160deg, #cfc6b8 0%, #b9a688 50%, #8a7a5c 100%); }
  .feature-photo { left: 488px; top: 0; width: 489px; height: 488px; background: linear-gradient(170deg, #2e2e2e 0%, #4f5a4a 40%, #7d8478 70%, #a7a59c 100%); }
  .feature-card { left: 548px; top: 76px; width: 372px; height: 338px; background: var(--white); text-align: center; }
  .card-mark { left: 160px; top: 38px; width: 52px; height: 83px; background: var(--plum); border-radius: 3px; }
  .card-rule { left: 111px; top: 140px; width: 150px; height: 2px; background: var(--ink); }
  .feature-title { left: 0; width: 372px; top: 160px; font-size: 25px; line-height: 33px; letter-spacing: 1px; font-weight: 500; }
  .btn-plum { background: var(--plum); color: var(--white); font-weight: 600; display: flex; align-items: center; justify-content: center; letter-spacing: .5px; }
  .feature-btn { left: 110px; top: 240px; width: 153px; height: 47px; font-size: 16px; }

  /* Story band */
  .story { left: 0; top: 1420px; width: 1200px; height: 1217px; background: var(--plum); color: var(--white); overflow: hidden; }
  .deco { border-radius: 50%; filter: blur(2px); }
  .deco-palm-a { left: -20px; top: 20px; width: 270px; height: 210px; background: radial-gradient(ellipse, #5f8a43 0%, rgba(95,138,67,.55) 50%, rgba(82,50,74,0) 72%); }
  .deco-rose-a { left: 1010px; top: 40px; width: 210px; height: 210px; background: radial-gradient(ellipse, #6d4a62 0%, rgba(61,40,52,.8) 45%, rgba(82,50,74,0) 72%); }
  .deco-rose-b { left: -30px; top: 405px; width: 230px; height: 190px; background: radial-gradient(ellipse, #6d4a62 0%, rgba(61,40,52,.8) 45%, rgba(82,50,74,0) 72%); }
  .deco-palm-b { left: 940px; top: 360px; width: 280px; height: 230px; background: radial-gradient(ellipse, #6f9a4d 0%, rgba(111,154,77,.55) 50%, rgba(82,50,74,0) 72%); }
  .story-title { left: 0; width: 1200px; top: 122px; text-align: center; font-size: 39px; line-height: 46px; letter-spacing: 1px; font-weight: 500; }
  .story-copy { left: 225px; width: 750px; top: 242px; text-align: center; font-size: 15px; line-height: 33px; }
  .btn-outline { left: 521px; top: 407px; width: 156px; height: 50px; border: 2px solid var(--white); border-radius: 3px; display: flex; align-items: center; justify-content: center; font-size: 16px; font-weight: 600; letter-spacing: .5px; }

  .service { top: 608px; width: 304px; height: 478px; background: var(--white); color: var(--ink); text-align: center; }
  .service-photo { left: 0; top: 0; width: 304px; height: 196px; }
  .photo-1 { background: linear-gradient(160deg, #1f3b36 0%, #5d6b56 50%, #c9bca4 100%); }
  .photo-2 { background: linear-gradient(160deg, #efe4d6 0%, #cbb99e 55%, #94a06f 100%); }
  .photo-3 { background: linear-gradient(160deg, #a7805c 0%, #c8a584 50%, #8a9a73 100%); }
  .service-name { left: 0; width: 304px; top: 228px; font-size: 23px; }
  .service-rule { left: 37px; top: 276px; width: 230px; height: 1px; background: var(--rule); }
  .service-meta { left: 0; width: 304px; font-size: 16px; }
  .service-btn { left: 87px; top: 394px; width: 131px; height: 41px; font-size: 13px; }

  /* Footer */
  .footer { left: 0; top: 2637px; width: 1200px; height: 631px; background: var(--sage); color: var(--white); font-size: 15px; font-weight: 600; }
  .foot-col { line-height: 31px; }
  .foot-rule { left: 111px; width: 978px; height: 1px; background: rgba(255,255,255,.55); }
  .checkbox { left: 110px; top: 538px; width: 37px; height: 36px; border: 1.5px solid var(--white); }
  .btn-submit { left: 901px; top: 535px; width: 189px; height: 47px; background: var(--white); color: var(--sage); display: flex; align-items: center; justify-content: center; font-size: 15px; letter-spacing: .5px; }

  .closing { left: 0; top: 3268px; width: 1200px; height: 106px; background: #fdf3f1; text-align: center; padding-top: 43px; font-size: 16px; font-weight: 500; }
</style>
</head>
<body>

<header>
  <nav class="abs nav"><span>Shop</span><span>Care</span><span>Our Story</span><span>Contact Us</span></nav>
  <div class="abs brand-mark" aria-hidden="true"></div>
  <div class="abs brand-name">THE WILLOWMERE ATELIER</div>
  <div class="abs login">
    <svg width="22" height="22" viewBox="0 0 22 22"><circle cx="11" cy="11" r="11" fill="#2b2226"/><circle cx="11" cy="8.5" r="3.6" fill="#fbefec"/><path d="M4.5 17.5c1.6-3 4-4.2 6.5-4.2s4.9 1.2 6.5 4.2" fill="#fbefec"/></svg>
    <span>Log In</span>
  </div>
  <svg class="abs cart" width="24" height="30" viewBox="0 0 24 30"><path d="M2 9h20v19H2z" fill="none" stroke="#2b2226" stroke-width="1.6"/><path d="M7 9V6a5 5 0 0 1 10 0v3" fill="none" stroke="#2b2226" stroke-width="1.6"/><text x="12" y="23" font-size="10" text-anchor="middle" font-family="Nunito, sans-serif" fill="#2b2226">0</text></svg>
</header>

<main>
  <div class="abs hero-photo" role="img" aria-label="Smiling woman reaching out in a sunlit rose garden with pink and cream blooms"></div>
  <section class="abs promo">
    <div class="abs promo-index">01 /</div>
    <div class="abs promo-text">3 free samples with any purchase</div>
    <div class="abs btn-light">SHOP NOW</div>
  </section>

  <section class="abs feature">
    <div class="abs feature-left">
      <div class="abs shot-a" role="img" aria-label="Wooden ladder shelf with potted houseplants"></div>
      <div class="abs shot-b" role="img" aria-label="Young potted tree beside a wooden-framed mirror"></div>
    </div>
    <div class="abs feature-photo" role="img" aria-label="Living room with monstera plants, rug and armchair"></div>
    <div class="abs feature-card">
      <div class="abs card-mark" aria-hidden="true"></div>
      <div class="abs card-rule"></div>
      <h2 class="abs feature-title serif">POTTED BEAUTY, READY<br>TO ROOT AT HOME</h2>
      <div class="abs btn-plum feature-btn">SHOP NOW</div>
    </div>
  </section>

  <section class="abs story">
    <div class="abs deco deco-palm-a" role="img" aria-label="Palm frond illustration"></div>
    <div class="abs deco deco-rose-a" role="img" aria-label="Dusky rose illustration"></div>
    <div class="abs deco deco-rose-b" role="img" aria-label="Dusky rose illustration"></div>
    <div class="abs deco deco-palm-b" role="img" aria-label="Palm frond illustration"></div>
    <h2 class="abs story-title serif">OUR JOURNEY FROM SEED TO<br>BLOSSOM</h2>
    <p class="abs story-copy">The Willowmere Atelier is dedicated to providing a curated collection of roses and blooming plants, carefully selected to bring joy and elegance to your home garden. Our team is committed to sharing our passion for plants and fostering a community of plant enthusiasts. Join us in celebrating the beauty of nature and the art of plant care.</p>
    <div class="abs btn-outline">SHOP NOW</div>

    <article class="abs service" style="left:111px">
      <div class="abs service-photo photo-1" role="img" aria-label="Potted cactus and leafy plants in ceramic pots"></div>
      <h3 class="abs service-name serif">Velmora Blush</h3>
      <div class="abs service-rule"></div>
      <div class="abs service-meta" style="top:336px">1 hr</div>
      <div class="abs service-meta" style="top:373px">$100</div>
      <div class="abs btn-plum service-btn">SHOP NOW</div>
    </article>
    <article class="abs service" style="left:448px">
      <div class="abs service-photo photo-2" role="img" aria-label="Houseplants on a wooden ladder shelf"></div>
      <h3 class="abs service-name serif">Velmora Blush</h3>
      <div class="abs service-rule"></div>
      <div class="abs service-meta" style="top:336px">1 hr</div>
      <div class="abs service-meta" style="top:373px">$100</div>
      <div class="abs btn-plum service-btn">SHOP NOW</div>
    </article>
    <article class="abs service" style="left:783px">
      <div class="abs service-photo photo-3" role="img" aria-label="Garden trowel and tools beside a potted succulent"></div>
      <h3 class="abs service-name serif">Velmora Blush</h3>
      <div class="abs service-rule"></div>
      <div class="abs service-meta" style="top:336px">1 hr</div>
      <div class="abs service-meta" style="top:373px">$100</div>
      <div class="abs btn-plum service-btn">SHOP NOW</div>
    </article>
  </section>
</main>

<footer class="abs footer">
  <div class="abs foot-col" style="left:123px;top:86px">Shop<br>About<br>Gift Card<br>FAQ<br>Contact<br>Book Online</div>
  <div class="abs foot-col" style="left:329px;top:86px;line-height:26px">218 Larkspur Lane, Guelph,<br>ON N1H 3T6</div>
  <div class="abs foot-col" style="left:329px;top:216px;line-height:26px">Opening Hours<br>Mon - Fri: 7am - 10pm<br>Saturday: 8am - 10pm</div>
  <div class="abs foot-col" style="left:629px;top:86px;line-height:26px">Customer Service<br><br>T: 519-555-0148<br>F: 519-555-0148<br><br>E: hello@willowmere.example</div>
  <div class="abs foot-col" style="left:893px;top:86px;line-height:26px">FAQ<br>Shipping &amp; Returns<br>Store Policy</div>
  <div class="abs foot-rule" style="top:368px"></div>
  <div class="abs" style="left:111px;top:408px">Subscribe to our mailing list</div>
  <div class="abs" style="left:113px;top:446px">Email*</div>
  <div class="abs foot-rule" style="top:504px"></div>
  <div class="abs checkbox"></div>
  <div class="abs" style="left:173px;top:546px">Yes, subscribe me to your newsletter.*</div>
  <div class="abs btn-submit">SUMBIT</div>
</footer>

<div class="abs closing">Proudly women-led and proudly Canadian</div>

</body>
</html>
```